Heron Loan Partners Business Card

We need a business card design for our mortgage servicing company. In addition to servicing the loans of homeowners, we help homeowners with purchasing their homes and any mortgage refinancing. We would like to see designs that use the colors in the logo attached below (gold-ish yellow and navy blue), and any other design you deem fit! The design should communicate a simpler life with smart mortgages provided by Heron.

```html
<!DOCTYPE html>
<html lang="en">
<head>
<meta charset="utf-8">
<title>Heron Loan Partners Business Card</title>
<link rel="stylesheet" href="https://fonts.googleapis.com/css2?family=Roboto:wght@400;500;700&display=swap">
<style>
  :root {
    --navy: #24204f;
    --gold: #c9a23a;
    --paper: #f6f6f8;
    --ink: #2a2a35;
    --rule: #cfcfd6;
    --stage: #e9e8ec;
  }
  * { margin: 0; padding: 0; box-sizing: border-box; }
  html, body { width: 1200px; height: 912px; overflow: hidden; }
  body {
    background: var(--stage);
    font-family: "Roboto", Arial, sans-serif;
    position: relative;
  }
  .card {
    position: absolute;
    width: 560px;
    height: 320px;
    box-shadow: 0 10px 26px rgba(0,0,0,.18);
    overflow: hidden;
  }
  /* Front */
  .card-front {
    left: 60px; top: 90px;
    background: var(--navy);
  }
  .card-front .brand-name {
    position: absolute;
    left: 0; right: 0; top: 118px;
    text-align: center;
    color: var(--gold);
    font-weight: 700;
    font-size: 40px;
    letter-spacing: .5px;
  }
  .card-front .web {
    position: absolute;
    left: 0; right: 0; top: 232px;
    text-align: center;
    color: #fff;
    font-size: 15px;
    letter-spacing: 3px;
  }
  .card-front .web .web-accent { color: var(--gold); }
  /* Back */
  .card-back {
    left: 580px; top: 502px;
    background: var(--paper);
  }
  .card-back .brand-name {
    position: absolute;
    left: 34px; top: 150px;
    width: 240px;
    color: var(--navy);
    font-weight: 700;
    font-size: 24px;
    text-align: center;
  }
  .divider {
    position: absolute;
    left: 296px; top: 32px;
    width: 1px; height: 190px;
    background: var(--rule);
    transform: rotate(-14deg);
    transform-origin: top;
  }
  .contact {
    position: absolute;
    left: 320px; top: 40px;
    color: var(--ink);
    font-size: 13.5px;
    line-height: 1.35;
  }
  .contact .person-name {
    color: var(--gold);
    font-weight: 700;
    font-size: 21px;
    line-height: 1.1;
  }
  .contact .person-title {
    color: var(--navy);
    font-size: 14px;
    margin-bottom: 10px;
  }
  .contact .address { margin-bottom: 10px; }
  .contact-line {
    display: flex;
    align-items: center;
    gap: 8px;
  }
  .contact-line svg { width: 11px; height: 11px; flex: none; }
  .band-gold {
    position: absolute;
    left: 0; bottom: 0;
    width: 430px; height: 16px;
    background: var(--gold);
  }
  .band-navy {
    position: absolute;
    left: 430px; bottom: 0;
    width: 130px; height: 16px;
    background: var(--navy);
  }
</style>
</head>
<body>
  <section class="card card-front">
    <div class="brand-name">Heron Loan Partners</div>
    <div class="web">www.<span class="web-accent">Heron</span>.com</div>
  </section>

  <section class="card card-back">
    <div class="brand-name">Heron Loan Partners</div>
    <div class="divider"></div>
    <div class="contact">
      <div class="person-name">Daniel Morrow</div>
      <div class="person-title">President</div>
      <div class="address">4120 Ashbury Lane<br>Glen Cove, NY 11542</div>
      <div class="contact-line">
        <svg viewBox="0 0 12 12"><path d="M2.5 1l2 2.2-1 1.3a7 7 0 0 0 4 4l1.3-1 2.2 2-1.2 1.5C5 11 1 7 1 2.2z" fill="var(--gold)"/></svg>
        <span>(555) 0147-2290</span>
      </div>
      <div class="contact-line">
        <svg viewBox="0 0 12 12"><rect x="0.5" y="2" width="11" height="8" fill="var(--gold)"/><path d="M0.5 2l5.5 4.5L11.5 2" fill="none" stroke="#fff" stroke-width="1"/></svg>
        <span>name@Heron.com</span>
      </div>
      <div class="contact-line">
        <svg viewBox="0 0 12 12"><circle cx="6" cy="6" r="5.5" fill="var(--gold)"/><path d="M0.5 6h11M6 0.5c-2.5 3-2.5 8 0 11M6 0.5c2.5 3 2.5 8 0 11" fill="none" stroke="#fff" stroke-width=".8"/></svg>
        <span>www.Heron.com</span>
      </div>
    </div>
    <div class="band-gold"></div>
    <div class="band-navy"></div>
  </section>
</body>
</html>
```